B2B Case Study Template Design (InDesign or Affinity Designer)

Hello,We are a company specializing in custom sanitary space fit-outs and Solid Surface manufacturing. We are looking for a talented layout designer to create a professional and modern "Case Study" template to showcase our projects.This template must strictly be designed using Adobe InDesign or Affinity Designer. We do not want Canva, Word, or PowerPoint files.Attached, there is a file you can reference named "Brelo - Case Study.pdf". This is our previous layout.

Your mission is to recreate this case study using our new brand guidelines (which I will also provide) while using the exact same texts, photos, and sections (Key Data / "Données clés", Valkor's Role / "Le rôle d'Valkor", Valkor Products / "Produits Valkor").

Note: This project is the first of a series. We want to keep everything in the same project scope moving forward. If the work is satisfactory, we will hire you directly for upcoming print materials (flyer templates, catalogs, etc.).

---
2 Exemples of existing Case Studies : BRELO and TOLVEN
1 Full INDISIGN assembled file for MURESK project (you can work from there)
The logo (multi format)
And a zip file with the PATTERN, FONT and LOGO ALTERNATIVES (for graphic use only - on a photo, or else)

Target Market(s)

Building professionals, architects, specifiers, B2B companies, and contractors.

Industry/Entity Type

Architecture / Construction / B2B

Font styles to use
Sans Serif

Requirements
Must have
• The final source file must be delivered in Adobe InDesign (.indd/.idml) or Affinity Designer format. The design must be clean, structured, and highlight the architectural photography. Paragraph and character styles must be properly set up in the software so we can easily edit the text ourselves in the future. Strict integration of our new brand guidelines (colors, typography).
Nice to have
• A modular design: a layout that works perfectly for a 2-page (front/back) document, but can be easily expanded to 3 or 4 pages if a specific case study requires more content. Layout suggestions for recurring graphic elements (e.g., custom icons for key data, elegant frames for pull quotes).
Should not have
• Do NOT use Canva, Microsoft Word, or Photoshop for the layout. Avoid cluttered, overly colorful, or whimsical designs. We are looking for a premium, high-end, and serious aesthetic suited for the architectural field.

```html
<!DOCTYPE html>
<html lang="fr">
<head>
<meta charset="utf-8">
<title>Case Study – BRELO Forest</title>
<link href="https://fonts.googleapis.com/css2?family=Poppins:wght@200;300;400;500;600;700&display=swap" rel="stylesheet">
<style>
  :root{
    --ink:#0a0a0a;
    --paper:#ffffff;
    --stage:#dcdcdc;
    --text:#1b1b1b;
    --panel:rgba(30,30,30,.88);
  }
  *{margin:0;padding:0;box-sizing:border-box}
  html,body{width:1200px;height:1200px;overflow:hidden;background:var(--stage);font-family:'Poppins',sans-serif;color:var(--text)}
  .board{position:relative;width:1200px;height:1200px}
  .page{position:absolute;width:560px;height:394px;overflow:hidden;background:var(--paper);box-shadow:0 6px 18px rgba(0,0,0,.15)}
  .page--cover{left:30px;top:196px;background:var(--ink)}
  .page--one{left:610px;top:196px}
  .page--two{left:30px;top:610px}
  .page--back{left:610px;top:610px;background:var(--ink);color:#fff}
  .abs{position:absolute}

  /* cover */
  .cover-visual{inset:0;position:absolute;background:linear-gradient(160deg,#0b0b0c 0%,#3a3c41 50%,#0b0b0c 100%)}
  .cover-title{left:0;right:0;top:160px;text-align:center;color:#fff;font-weight:200;font-size:38px;letter-spacing:.5px}
  .cover-sub{left:0;right:0;top:213px;text-align:center;color:#fff;font-weight:400;font-size:13px}
  .brand{color:#fff;font-weight:500;letter-spacing:4px}
  .cover-brand{right:28px;bottom:24px;font-size:12px}

  /* inner pages */
  .strip{top:0;bottom:0;width:31px;background:var(--ink)}
  .folio{bottom:12px;width:31px;text-align:center;color:#fff;font-size:6px}
  .headline{font-size:17px;line-height:1.2;color:var(--ink)}
  .headline b{font-weight:600}
  .headline span{font-weight:400;white-space:nowrap}
  .lead{font-size:9.5px;line-height:1.3;font-weight:500;color:var(--ink)}
  .body{font-size:6.8px;line-height:1.45;font-weight:400;margin-top:8px}
  .section-head{font-size:8.5px;font-weight:600;margin-top:14px;color:var(--ink)}
  .list{list-style:none;font-size:6.5px;line-height:1.5;margin-top:5px}
  .list li{padding-left:8px;position:relative}
  .list li::before{content:"•";position:absolute;left:0}
  .list b{font-weight:600}
  .block{background:var(--ink)}
  .photo{background:linear-gradient(160deg,#3f4637 0%,#5b6350 35%,#cfcac2 62%,#8a6a4c 85%,#4a4038 100%)}
  .photo--narrow{background:linear-gradient(170deg,#4b4a42 0%,#77766a 30%,#e4ddd2 55%,#9a7552 80%,#5a4c3e 100%)}
  .products{background:var(--panel);padding:10px 10px 8px;color:#fff}
  .products h4{font-size:7.5px;font-weight:600;letter-spacing:.3px;margin-bottom:7px}
  .product-row{display:flex;gap:10px}
  .product{flex:1;text-align:center}
  .product-shot{height:38px;background:linear-gradient(180deg,#f2f2f2,#d6d6d6)}
  .product p{font-size:5px;line-height:1.3;margin-top:5px;text-transform:uppercase}

  /* back */
  .back-brand{left:0;right:0;top:160px;text-align:center;font-size:30px}
  .contact-title{left:34px;top:283px;font-size:8px;font-weight:600}
  .contact-col{top:303px;font-size:6px;line-height:1.5}
  .contact-col .label{margin-bottom:8px}
</style>
</head>
<body>
<main class="board">

  <section class="page page--cover">
    <div class="cover-visual" role="img" aria-label="Visuel abstrait de drapé satiné noir aux reflets argentés"></div>
    <h1 class="abs cover-title">Case Study</h1>
    <p class="abs cover-sub">BRELO Forest</p>
    <div class="abs brand cover-brand">ORVANE</div>
  </section>

  <section class="page page--one">
    <div class="abs strip" style="left:0"></div>
    <div class="abs folio" style="left:0">1</div>
    <div class="abs block" style="left:402px;top:0;width:158px;height:394px"></div>

    <div class="abs" style="left:49px;top:46px;width:212px">
      <h2 class="headline"><b>Projet Muresk:</b><br><span>quand la performance</span><br><span>s'adapte à la continuité</span></h2>
      <p class="body">L'enjeu majeur du chantier Muresk résidait dans l'environnement immédiat : des open spaces occupés par des collaborateurs en plein travail.</p>
      <p class="body">Ce projet exigeait donc une discrétion absolue et une rapidité d'exécution chirurgicale, dans le but de maintenir le confort des usagers pendant la transformation des espaces sanitaires.</p>
      <h3 class="section-head">DONNÉES CLÉ</h3>
      <ul class="list">
        <li><b>Lieu</b> : 12 Rue Delorme, Paris 17e (immeuble bureaux Premium)</li>
        <li><b>Maître d'ouvrage</b> : Sorel Banque</li>
        <li><b>Maître d'œuvre</b> : Kelto</li>
        <li><b>Livraison</b> : 2025</li>
      </ul>
      <h3 class="section-head">LE RÔLE D'VALKOR</h3>
      <ul class="list">
        <li>Conception de mobilier VERANIT sur-mesure à profondeur variable</li>
        <li>Planification de pose par tranches</li>
        <li>Logistique de propreté «Zéro Poussière»</li>
        <li>Installation en mode «Discret»</li>
      </ul>
    </div>

    <div class="abs photo" style="left:279px;top:44px;width:246px;height:320px" role="img" aria-label="Photographie d'un sanitaire rénové avec double vasque blanche, miroir et murs vert olive"></div>

    <div class="abs products" style="left:289px;top:258px;width:230px;height:108px">
      <h4>PRODUITS VALKOR</h4>
      <div class="product-row">
        <div class="product"><div class="product-shot" role="img" aria-label="Vasque blanche avec robinetterie"></div><p>Vasque Orla<br>J2210</p></div>
        <div class="product"><div class="product-shot" role="img" aria-label="Support de vasque sur-mesure"></div><p>Support Veranit<br>sur-mesure</p></div>
        <div class="product"><div class="product-shot" role="img" aria-label="Miroir sur mesure"></div><p>Miroir<br>sur mesure</p></div>
      </div>
    </div>
  </section>

  <section class="page page--two">
    <div class="abs block" style="left:0;top:0;width:156px;height:394px"></div>
    <div class="abs strip" style="left:529px"></div>
    <div class="abs folio" style="left:529px">2</div>
    <div class="abs photo--narrow" style="left:33px;top:34px;width:182px;height:329px" role="img" aria-label="Photographie d'un lave-mains blanc sur meuble bois dans un sanitaire étroit"></div>

    <div class="abs" style="left:245px;top:44px;width:265px">
      <h2 class="headline"><b>Une prouesse d'agilité:</b><br><span>le défi du site occupé</span></h2>
      <p class="lead" style="margin-top:14px">Maintenir le confort des usagers pendant la mutation des espaces.</p>
      <p class="body">L'enjeu majeur du chantier Muresk résidait dans l'environnement immédiat : des open spaces occupés par des collaborateurs en plein travail.</p>
      <p class="body">Ce projet « Muresk » exigeait donc une discrétion absolue et une rapidité d'exécution chirurgicale.</p>
      <p class="lead" style="margin-top:14px">1. Mode «Discret» &amp; propreté :</p>
      <p class="body">Travailler dans le silence et sans dégagement de poussière était une condition non négociable.</p>
      <p class="body">Valkor a mis en place un protocole spécifique pour garantir une propreté absolue des parties communes et des sanitaires, permettant aux occupants de continuer leurs activités sans nuisance.</p>
      <p class="lead" style="margin-top:14px">2. Flux de travail «Chrono»</p>
      <p class="body">Pour éviter la fermeture simultanée de tous les sanitaires de l'immeuble, Valkor a orchestré une pose par tranches successives.</p>
      <p class="body">Ce phasage dynamique a permis de maintenir la continuité de service pour le client tout en assurant un temps de travaux record par étage.</p>
    </div>
  </section>

  <section class="page page--back">
    <div class="abs brand back-brand">ORVANE</div>
    <p class="abs contact-title">Prendre contact.</p>
    <div class="abs contact-col" style="left:34px"><p class="label">Adresse</p><p>Rue des Prés,<br>43200 Montclair<br>France.</p></div>
    <div class="abs contact-col" style="left:148px"><p class="label">Site Web</p><p>www.valkor.fr<br>info@valkor.fr</p></div>
    <div class="abs contact-col" style="left:226px"><p class="label">Téléphone</p><p>+33 4 00 00 00 00</p></div>
  </section>

</main>
</body>
</html>
```